Bramblewood Card Company Business Cards

We are a trading card store with Glimmorax, sports and other TCG cards, we need a business card design that encompasses a clean cut, modern style with a retro flare. website is bramblewoodcardco.com for reference. Can utilize a comic book era feel or a more modern outdoor feel to utilize the "Pacific Northwest" elements of tress, mountains, etc.

Industry/Entity Type

Trading cards and collectibles

Contact Information for Business Card

business name, email address, phone number, name, owner job title

Font styles to use
Sans Serif

```html
<!DOCTYPE html>
<html lang="en">
<head>
<meta charset="utf-8">
<title>Bramblewood Card Company – Business Cards</title>
<link rel="stylesheet" href="https://fonts.googleapis.com/css2?family=Montserrat:wght@400;600;700&display=swap">
<style>
  :root {
    --backdrop: #d4d7d8;
    --card-white: #f7f7f5;
    --brand-cyan: #0db4d9;
    --brand-cyan-deep: #0a93b3;
    --ink-charcoal: #3d3e40;
    --ink-text: #2b2b2d;
    --card-shadow: 0 18px 40px rgba(40, 50, 55, 0.22);
  }
  * { box-sizing: border-box; margin: 0; padding: 0; }
  html, body {
    width: 1200px;
    height: 829px;
    overflow: hidden;
    background: var(--backdrop);
    font-family: "Montserrat", Arial, sans-serif;
  }
  .sheet {
    position: relative;
    width: 1200px;
    height: 829px;
    display: flex;
    align-items: center;
    justify-content: center;
    gap: 44px;
  }
  .card {
    width: 520px;
    height: 297px;
    border-radius: 3px;
    box-shadow: var(--card-shadow);
    position: relative;
    overflow: hidden;
  }

  /* Front */
  .card--front {
    background: var(--card-white);
    border-bottom: 4px solid var(--brand-cyan);
    display: flex;
    align-items: center;
    padding: 0 34px 0 36px;
    gap: 30px;
  }
  .brand-mark {
    display: flex;
    align-items: center;
    gap: 10px;
    width: 188px;
  }
  .brand-mark__square {
    flex: none;
    width: 26px;
    height: 26px;
    background: var(--brand-cyan);
  }
  .brand-mark__name {
    font-weight: 700;
    font-size: 17px;
    line-height: 1.15;
    text-transform: uppercase;
    letter-spacing: 0.04em;
    color: var(--ink-charcoal);
  }
  .contact {
    flex: 1;
    color: var(--ink-text);
    font-size: 12.5px;
    line-height: 1.45;
  }
  .contact__name {
    font-weight: 700;
    font-size: 21px;
    letter-spacing: 0.08em;
    text-transform: uppercase;
    color: var(--brand-cyan);
    line-height: 1.1;
  }
  .contact__title { font-size: 13px; }
  .contact__rule {
    width: 10px;
    height: 1px;
    background: var(--ink-text);
    margin: 7px 0;
  }
  .contact__list { list-style: none; }
  .contact__item {
    display: flex;
    align-items: center;
    gap: 7px;
  }
  .contact__icon {
    width: 10px;
    height: 10px;
    flex: none;
    fill: var(--brand-cyan);
  }

  /* Back */
  .card--back {
    background: var(--brand-cyan);
    border-bottom: 4px solid var(--brand-cyan-deep);
    display: flex;
    align-items: center;
    justify-content: center;
  }
  .card--back .brand-mark {
    width: auto;
    gap: 14px;
  }
  .card--back .brand-mark__circle {
    flex: none;
    width: 34px;
    height: 34px;
    border-radius: 50%;
    background: var(--ink-charcoal);
  }
  .card--back .brand-mark__name {
    font-size: 22px;
  }
</style>
</head>
<body>
<main class="sheet">
  <section class="card card--front" aria-label="Business card front">
    <div class="brand-mark">
      <span class="brand-mark__square" aria-hidden="true"></span>
      <span class="brand-mark__name">Bramblewood Card Company</span>
    </div>
    <div class="contact">
      <p class="contact__name">Elias Marrow</p>
      <p class="contact__title">CEO/Founder</p>
      <div class="contact__rule"></div>
      <p>P.O. Box 3187 Fernhill Road<br>Cedar Vale WA 98512</p>
      <div class="contact__rule"></div>
      <ul class="contact__list">
        <li class="contact__item">
          <svg class="contact__icon" viewBox="0 0 10 10" aria-hidden="true"><path d="M2 0.5 L3.6 2.6 L2.7 3.6 Q3.6 5.6 6.4 7.3 L7.4 6.4 L9.5 8 L8.2 9.5 Q2 8.6 0.5 1.8 Z"/></svg>
          (555) 014 2738
        </li>
        <li class="contact__item">
          <svg class="contact__icon" viewBox="0 0 10 10" aria-hidden="true"><path d="M0 2 H10 V8.5 H0 Z M0.6 2.4 L5 5.6 L9.4 2.4" stroke="#f7f7f5" stroke-width="0.8"/></svg>
          info@bramblewoodcardco.com
        </li>
        <li class="contact__item">
          <svg class="contact__icon" viewBox="0 0 10 10" aria-hidden="true"><circle cx="5" cy="5" r="4.6"/><path d="M0.5 5 H9.5 M5 0.5 V9.5 M1.5 2.8 H8.5 M1.5 7.2 H8.5" stroke="#f7f7f5" stroke-width="0.6" fill="none"/></svg>
          www.bramblewoodcardco.com
        </li>
      </ul>
    </div>
  </section>

  <section class="card card--back" aria-label="Business card back">
    <div class="brand-mark">
      <span class="brand-mark__circle" aria-hidden="true"></span>
      <span class="brand-mark__name">Bramblewood Card Company</span>
    </div>
  </section>
</main>
</body>
</html>
```